Real Estate Newsletter

I would like a template created for a monthly newsletter; ideally, two pages long, including my photo, logo and contact info. I need it to look professional and be very easy for me to drop text into.

Target Market(s)

Past/current clients

Industry/Entity Type

Real Estate Agent

Font styles to use
Serif

Requirements
Must have
• My contact info/photo and logo
• (206) 555-0173
• mkorvell@tlxhb.com
• www.MarenKorvell.com
Nice to have
• I need a template where I can easily drop contact. I need the template to look professional so I can print it and mail it to current and past clients.

```html
<!DOCTYPE html>
<html lang="en">
<head>
<meta charset="utf-8">
<title>Maren Korvell – Newsletter</title>
<link href="https://fonts.googleapis.com/css2?family=Libre+Baskerville:wght@400;700&display=swap" rel="stylesheet">
<style>
  :root {
    --frame: #d6d7db;
    --paper: #ffffff;
    --band: #c8cbe6;
    --navy: #2b3a96;
    --ring: #8f97cf;
    --ink: #1a1a1a;
    --photo-a: #b7a28e;
    --photo-b: #e9e4de;
  }
  * { margin: 0; padding: 0; box-sizing: border-box; }
  html, body { width: 1200px; height: 1200px; overflow: hidden; background: var(--paper); }
  .canvas { position: relative; width: 1200px; height: 1200px; background: var(--paper); }
  .frame { position: absolute; left: 56px; top: 50px; width: 1102px; height: 1102px; background: var(--frame); }
  .page { position: absolute; left: 77px; top: 76px; width: 1055px; height: 1054px; background: var(--paper); }
  .header-band { position: absolute; left: 0; top: 0; }
  .agent-name {
    position: absolute; left: 0; top: 160px; width: 1200px; text-align: center;
    font-family: "Libre Baskerville", serif; font-weight: 400; font-size: 38px;
    color: var(--navy); letter-spacing: 0.5px;
  }
  .agent-contact {
    position: absolute; left: 0; top: 212px; width: 1200px; text-align: center;
    font-family: "Libre Baskerville", serif; font-size: 12.5px; color: var(--navy); letter-spacing: 0.6px;
  }
  .agent-contact span + span::before { content: "•"; margin: 0 10px; }
  .portrait {
    position: absolute; left: 269px; top: 303px; width: 140px; height: 140px; border-radius: 50%;
    background: radial-gradient(circle at 50% 45%, var(--photo-b) 0%, var(--photo-a) 70%, #8a6e58 100%);
    box-shadow: 0 0 0 4px var(--ring);
  }
  .dash-h { position: absolute; border-top: 2px dashed var(--navy); }
  .dash-v { position: absolute; left: 505px; top: 302px; height: 766px; border-left: 2px dashed var(--navy); }
  .section-title { position: absolute; font-family: "Libre Baskerville", serif; font-weight: 400; color: var(--navy); }
  .about-title { right: 774px; top: 481px; font-size: 18px; letter-spacing: 2.5px; }
  .about-text {
    position: absolute; right: 776px; top: 526px; width: 230px; text-align: right;
    font-family: "Libre Baskerville", serif; font-size: 12.5px; line-height: 16.1px;
    color: var(--navy); letter-spacing: 0.9px; white-space: nowrap;
  }
  .testimonial-title { left: 578px; width: 484px; text-align: center; top: 350px; font-size: 21px; letter-spacing: 0.8px; }
  .testimonial {
    position: absolute; left: 578px; width: 484px;
    font-family: "Libre Baskerville", serif; font-size: 13.3px; line-height: 17.95px; color: var(--ink);
  }
  .testimonial span { display: block; text-align: justify; text-align-last: justify; white-space: nowrap; }
  .testimonial span.end { text-align-last: left; }
  .testimonial span.indent { padding-left: 26px; }
  .t-one { top: 418px; }
  .t-two { top: 794px; }
</style>
</head>
<body>
<div class="canvas">
  <div class="frame"></div>
  <div class="page"></div>
  <svg class="header-band" width="1200" height="280" viewBox="0 0 1200 280" aria-hidden="true">
    <polygon points="158,76 1055,76 1055,236 606,266 158,236" fill="var(--band)"/>
  </svg>
  <div class="agent-name">Maren Korvell</div>
  <div class="agent-contact"><span>(206) 555-0173</span><span>mkorvell@tlxhb.com</span><span>www.MarenKorvell.com</span></div>

  <div class="portrait" role="img" aria-label="Portrait photo of Maren Korvell"></div>

  <div class="dash-h" style="left:173px; top:474px; width:253px;"></div>
  <h2 class="section-title about-title">ABOUT ME</h2>
  <div class="dash-h" style="left:173px; top:508px; width:253px;"></div>
  <p class="about-text">
    I have spent my entire<br>life in the Seattle area. I<br>was born and raised in<br>Greenlake- before Ballard<br>and Greenlake were<br>"cool" areas- back when<br>they were still small,<br>sleepy Seattle neighbor-<br>hoods.<br>It was my husband who<br>first introduced me to<br>real estate. His father<br>had made a living pur-<br>chasing homes, rehab-<br>bing them and turning<br>them into long term<br>rental properties. At his<br>encouragement, we pur-<br>chased our first home- a<br>run down shack literally<br>encroaching on an off<br>ramp of I5. I couldn't see<br>the vision, but blindly<br>followed. Fast forward 7+<br>years and we own a<br>handful of rental proper-<br>ties throughout Seattle,<br>Shoreline and Lake<br>Forest Park that we've re-<br>habbed and manage our-<br>selves.
  </p>

  <div class="dash-v"></div>

  <h2 class="section-title testimonial-title">Client Testimoni</h2>
  <div class="dash-h" style="left:578px; top:390px; width:484px;"></div>

  <p class="testimonial t-one">
    <span class="indent">Maren is amazing! She helped us get top dollar for</span>
    <span>our old home, and to make a competitive offer on our</span>
    <span>new one that secured us the house of our dreams. We</span>
    <span>must have toured through 15-20 different houses look-</span>
    <span>ing for our dream home. She was so insightful and</span>
    <span>helpful as we tried to decide, as my husband and I had</span>
    <span>some different must-haves. Once we decided on the</span>
    <span>house for us, she crafted a strategy that enabled us to</span>
    <span>beat the competition without throwing all our money</span>
    <span>on the table. I felt we got our house for a fair price - and</span>
    <span>she was right on the money when it came to her pre-</span>
    <span>dicted final sale price. She helped us clean, stage and</span>
    <span>sell our old home and get a quick close that met our</span>
    <span>sales goal. Her great sales skills helped ensure we re-</span>
    <span>ceived several good offers to choose from. I LOVE our</span>
    <span>new house and hope we never have to move again - but</span>
    <span>if we do, I know who I’ll call. I can’t recommend her</span>
    <span>highly enough, and am always referring family and</span>
    <span>friends her way. Thanks so much Maren! &nbsp;&nbsp;&nbsp;&nbsp;&nbsp;- Laurel</span>
    <span class="end">&amp; Tobin Ashgrove, Shoreline</span>
  </p>

  <p class="testimonial t-two">
    <span class="indent">We were looking for a single family home in the Lake</span>
    <span>Forest Park area and we wanted an agent who knew the</span>
    <span>neighborhood and could guide us through our first</span>
    <span>home purchase. We are glad we chose Maren. She is</span>
    <span>honest and has a go-getter personality that is necessary</span>
    <span>in this competitive market. She was never pushy, gave</span>
    <span>us the best advice on making our offer competitive and</span>
    <span>we could not be more happy with her. We have no hesi-</span>
    <span>tation referring her to family and friends! &nbsp;&nbsp;- Daniel</span>
    <span class="end">&amp; Priya Vossberg, Lake Forest Park</span>
  </p>
</div>
</body>
</html>
```